Kestrel Home Business Card Design

We need a business card for a Building company based in Queensland, Australia. Our colours are orange black and we do base all our homes design names and other aspect of our business on astrology. We want the consumer to perceive the company as professional and to attract investors to our company.We have over 20 years in the building industry.We pride ourselves on our innovation of designs and making the building process for anyone from families to investor a smooth and simple experience.
Business
Amelia Prichard0411752116PO Box 454, Mudgeerbaameliaprichard@zodiachomes.com

```html
<!DOCTYPE html>
<html lang="en">
<head>
<meta charset="utf-8">
<title>Kestrel Homes – Business Card</title>
<link rel="stylesheet" href="https://fonts.googleapis.com/css2?family=Open+Sans:wght@400;600;700;800&display=swap">
<style>
  :root {
    --orange: #f7931e;
    --orange-deep: #f0851a;
    --black: #0b0b0b;
    --ink: #1a1a1a;
    --backdrop: #e9ecec;
    --card-w: 620px;
    --card-h: 378px;
  }
  * { box-sizing: border-box; margin: 0; padding: 0; }
  html, body {
    width: 1200px; height: 900px; overflow: hidden;
    background: var(--backdrop);
    font-family: "Open Sans", Arial, sans-serif;
  }
  .sheet {
    width: 1200px; height: 900px;
    display: flex; flex-direction: column; align-items: center; justify-content: center;
    gap: 56px;
  }
  .card {
    position: relative;
    width: var(--card-w); height: var(--card-h);
    background: var(--orange);
    overflow: hidden;
    box-shadow: 0 6px 18px rgba(0,0,0,.12);
  }

  /* Front side */
  .card-front .black-field {
    position: absolute; inset: 0; width: 100%; height: 100%;
  }
  .brand-mark {
    position: absolute; top: 46px; right: 44px;
    display: flex; align-items: center; gap: 14px;
  }
  .brand-dot {
    width: 52px; height: 52px; border-radius: 50%;
    background: var(--orange);
    flex: none;
  }
  .brand-name {
    font-weight: 800; letter-spacing: .5px; white-space: nowrap;
  }
  .card-front .brand-name { color: var(--orange); font-size: 30px; }

  .contact {
    position: absolute; left: 44px; bottom: 44px;
    color: var(--ink);
  }
  .contact-name {
    font-weight: 700; font-size: 24px; letter-spacing: 1px; margin-bottom: 12px;
  }
  .contact-list { list-style: none; }
  .contact-list li {
    display: flex; align-items: center; gap: 12px;
    font-size: 15.5px; line-height: 24px; letter-spacing: .6px;
  }
  .contact-list svg { width: 14px; height: 14px; flex: none; fill: #fff; }

  /* Back side */
  .card-back { display: flex; align-items: center; justify-content: center; }
  .card-back .brand-lockup { display: flex; align-items: center; gap: 26px; }
  .card-back .brand-dot {
    width: 118px; height: 118px;
    background: var(--black);
    border: 7px solid #fff;
    box-shadow: 0 0 0 3px var(--black);
  }
  .card-back .brand-name { color: var(--black); font-size: 52px; }
</style>
</head>
<body>
  <main class="sheet">

    <section class="card card-front" aria-label="Business card front">
      <svg class="black-field" viewBox="0 0 620 378" preserveAspectRatio="none" aria-hidden="true">
        <polygon points="0,0 620,0 620,240 0,150" fill="#0b0b0b"/>
      </svg>

      <div class="brand-mark">
        <span class="brand-dot"></span>
        <span class="brand-name">Kestrel Homes</span>
      </div>

      <div class="contact">
        <p class="contact-name">Harriet Colvane</p>
        <ul class="contact-list">
          <li>
            <svg viewBox="0 0 16 16" aria-hidden="true"><path d="M3.6 1.2l2.3 2.6-1.3 1.8c.9 2 2.8 3.9 4.8 4.8l1.8-1.3 2.6 2.3-1.4 2.3C7 13.5 2.5 9 1.3 2.6z"/></svg>
            <span>0487309625</span>
          </li>
          <li>
            <svg viewBox="0 0 16 16" aria-hidden="true"><path d="M8 0.8a5 5 0 0 0-5 5c0 3.8 5 9.4 5 9.4s5-5.6 5-9.4a5 5 0 0 0-5-5zm0 7a2 2 0 1 1 0-4 2 2 0 0 1 0 4z"/></svg>
            <span>PO Box 872, Tallowbrook</span>
          </li>
          <li>
            <svg viewBox="0 0 16 16" aria-hidden="true"><path d="M1 3h14v10H1zM2.2 4.2v.4L8 8.6l5.8-4v-.4zM2.2 6v5.8h11.6V6L8 10z"/></svg>
            <span>harrietcolvane@kestrelhomes.example</span>
          </li>
        </ul>
      </div>
    </section>

    <section class="card card-back" aria-label="Business card back">
      <div class="brand-lockup">
        <span class="brand-dot"></span>
        <span class="brand-name">Kestrel Homes</span>
      </div>
    </section>

  </main>
</body>
</html>
```